Refresh of a Media Kit for Adtech Company - Needs jazzing up!

We have a Media Kit that's too ugly and boring to send to clients. Attaching some examples of ones we like better. Keep the general styling and theme of the current media kit (it's our brand style) and all the information conveyed, but please change anything and everything else to make it more dynamic. Attaching examples of media kits we like.

The "Media Kit Vantor" is the one you're designing, the others are just examples of media kits we liked.
Updates

Here's a link to "Glamour Shots" that can be used as appropriate throughout the Media kit: https://www.filquarry.net/sh/q7mzkx31rwp8tnb/BXK4Pqwertz_LM9nVwYdQaHfZ?dl=0

Target Market(s)

Demand partners

Colors
0592cd
85cae6
34a7d8

Requirements
Nice to have
• Here are some glamour shots you can use if you see a good fit for any of them: https://www.filquarry.net/sh/q7mzkx31rwp8tnb/BXK4Pqwertz_LM9nVwYdQaHfZ?dl=0

```html
<!DOCTYPE html>
<html lang="en">
<head>
<meta charset="utf-8">
<title>Media Kit Vantor – Inventory Highlights</title>
<link href="https://fonts.googleapis.com/css2?family=Roboto:wght@300;400;700&display=swap" rel="stylesheet">
<style>
  :root{
    --page-bg:#e6e7e8;
    --slide-bg:#ffffff;
    --brand-blue:#0592cd;
    --icon-blue:#1e8fe6;
    --soft-blue:#85cae6;
    --mid-blue:#34a7d8;
    --badge-grey:#dadada;
    --ink:#2b2b2b;
    --muted:#555a5f;
    --divider:#d6d9dc;
    --page-num:#9a9a9a;
  }
  *{box-sizing:border-box;margin:0;padding:0}
  html,body{width:1200px;height:724px;overflow:hidden}
  body{background:var(--page-bg);font-family:'Roboto',Arial,sans-serif;color:var(--ink);position:relative}
  .slide{position:absolute;width:544px;height:306px;background:var(--slide-bg);overflow:hidden}
  .slide--medical{left:39px;top:40px}
  .slide--retail{left:617px;top:40px}
  .slide--entertainment{left:39px;top:377px}
  .slide--networth{left:617px;top:377px}

  .slide-title{position:absolute;font-weight:300;font-size:19.5px;line-height:1.25;color:var(--ink);white-space:nowrap}
  .slide-title strong{font-weight:700;color:#1f1f1f}

  .segment{position:absolute;font-weight:300;font-size:10px;color:var(--ink);white-space:nowrap}
  .segment b{font-weight:700}
  .segment::after{content:"";position:absolute;left:0;top:15px;width:35px;height:2.5px;background:var(--soft-blue)}

  .divider{position:absolute;width:1px;background:var(--divider)}

  .stat{position:absolute;width:90px;text-align:center;
        left:calc(var(--x) * 1px - 45px);top:calc(var(--y) * 1px - 17.5px)}
  .stat__icon{display:block;width:35px;height:35px;margin:0 auto;border-radius:50%;background:var(--icon-blue)}
  .stat__icon svg{width:35px;height:35px;display:block}
  .stat__label{margin-top:3px;font-size:7.2px;font-weight:300;line-height:1.25;color:var(--muted)}
  .stat--large .stat__icon{width:39px;height:39px}
  .stat--large .stat__icon svg{width:39px;height:39px}
  .stat--large{top:calc(var(--y) * 1px - 19.5px)}

  .photo{position:absolute;top:0;height:306px}
  .photo--medical{left:310px;width:234px;border-radius:48px 0 0 48px;
    background:linear-gradient(180deg,#dfe4e8 0%,#c9cfd6 45%,#e9e2d5 60%,#d8cbb4 100%)}
  .photo--retail{left:0;width:225px;border-radius:0 48px 48px 0;
    background:linear-gradient(160deg,#7a5a3c 0%,#b8492f 25%,#3f6aa8 50%,#3b3a44 75%,#c9cdd6 100%)}
  .photo--entertainment{left:292px;width:252px;border-radius:48px 0 0 48px;
    background:linear-gradient(180deg,#6b4a2e 0%,#8c6a45 30%,#3a2e26 55%,#1f2330 75%,#9aa7b8 100%)}
  .photo--networth{left:0;width:260px;border-radius:0 48px 48px 0;
    background:linear-gradient(180deg,#5a3a1e 0%,#8a5f31 35%,#c89b5c 70%,#e0c08c 100%)}

  .title-plate{position:absolute;left:0;top:26px;height:34px;width:352px;background:var(--slide-bg)}

  .badge-exclusive{position:absolute;width:52px;height:52px;border-radius:50%;background:var(--badge-grey);
    display:flex;align-items:center;justify-content:center;text-align:center;color:#fff;
    font-size:7.6px;font-weight:300;line-height:1.25}
  .badge-exclusive span{transform:rotate(-32deg)}

  .badge-feature{position:absolute;width:78px;height:78px;border-radius:50%;background:var(--soft-blue);
    display:flex;flex-direction:column;align-items:center;justify-content:center;text-align:center;color:#fff;
    font-size:7.2px;font-weight:300;line-height:1.25}
  .badge-feature svg{width:26px;height:26px;margin-bottom:3px}
  .badge-feature--tilted span{transform:rotate(-30deg);font-size:8.4px}

  .footer{position:absolute;top:290px;display:flex;align-items:center;gap:14px}
  .footer__tag{font-size:7px;font-weight:400;letter-spacing:4.4px;color:var(--icon-blue)}
  .brand{display:flex;align-items:center;gap:2px;font-size:7.6px;font-weight:700;color:var(--icon-blue)}
  .brand__mark{width:8px;height:8px;background:var(--icon-blue);border-radius:1px}
  .footer--light .footer__tag,.footer--light .brand{color:#fff}
  .footer--light .brand__mark{background:#fff}

  .page-number{position:absolute;left:1162px;top:676px;font-size:36px;font-weight:700;color:var(--page-num)}
</style>
</head>
<body>

<svg width="0" height="0" style="position:absolute" aria-hidden="true">
  <defs>
    <symbol id="i-play" viewBox="0 0 36 36"><g fill="none" stroke="#fff" stroke-width="1.6" stroke-linejoin="round"><rect x="10" y="10" width="16" height="16" rx="2.5"/><path d="M16 14.5v7l5.5-3.5z"/></g></symbol>
    <symbol id="i-globe" viewBox="0 0 36 36"><g fill="none" stroke="#fff" stroke-width="1.6"><circle cx="18" cy="17" r="7.5"/><path d="M13 13.5c3 1 3 4 5 4.5s2.5 3 1.5 5.5M21 10.5c-1 2 1 3 3 3"/><path d="M18 24.5v3"/></g></symbol>
    <symbol id="i-expand" viewBox="0 0 36 36"><g fill="none" stroke="#fff" stroke-width="1.6" stroke-linecap="round"><rect x="15" y="15" width="6" height="6"/><path d="M9 13V9h4M9 9l4.5 4.5M27 13V9h-4M27 9l-4.5 4.5M9 23v4h4M9 27l4.5-4.5M27 23v4h-4M27 27l-4.5-4.5"/></g></symbol>
    <symbol id="i-viewer" viewBox="0 0 36 36"><g fill="none" stroke="#fff" stroke-width="1.6"><path d="M8 16c3-4 6-6 10-6s7 2 10 6"/><path d="M8 16c2 2.5 4 4 6.5 4.8"/><circle cx="17" cy="15.5" r="2.5"/><circle cx="22.5" cy="19" r="2.3"/><path d="M18.5 27c0-3 1.8-4.5 4-4.5s4 1.5 4 4.5z"/></g></symbol>
    <symbol id="i-dwell" viewBox="0 0 36 36"><g fill="none" stroke="#fff" stroke-width="1.6"><circle cx="14" cy="12" r="2.5"/><path d="M10 27v-7l4-4 3 4h4M14 16l-1 5"/><circle cx="23" cy="13" r="4.5"/><path d="M23 10.5V13h2"/></g></symbol>
    <symbol id="i-income" viewBox="0 0 36 36"><g fill="none" stroke="#fff" stroke-width="1.6"><circle cx="15" cy="16" r="5"/><path d="M15 13v6M13.5 14.5h2.5a1 1 0 010 2h-1.5a1 1 0 000 2H17"/><circle cx="23" cy="11" r="2"/><path d="M20 27v-8l3-3 3 3v8M23 20v7"/></g></symbol>
    <symbol id="i-pill" viewBox="0 0 36 36"><g fill="none" stroke="#fff" stroke-width="1.6"><circle cx="14" cy="13" r="5"/><path d="M9 13h10"/><rect x="17" y="17" width="12" height="6" rx="3" transform="rotate(-40 23 20)"/></g></symbol>
    <symbol id="i-spot" viewBox="0 0 36 36"><g fill="none" stroke="#fff" stroke-width="1.6"><path d="M15 28s-6-7-6-12a6 6 0 0112 0c0 5-6 12-6 12z"/><path d="M15 13v6M13.5 14.5h2.5a1 1 0 010 2"/><path d="M23 16h4M22 22h3v5" stroke-dasharray="2 1.5"/></g></symbol>
    <symbol id="i-field" viewBox="0 0 36 36"><g fill="none" stroke="#fff" stroke-width="1.6"><rect x="6" y="10" width="24" height="16" rx="1"/><path d="M18 10v16"/><circle cx="18" cy="18" r="3"/><path d="M6 14h3v8H6M30 14h-3v8h3"/></g></symbol>
  </defs>
</svg>

<!-- Medical -->
<section class="slide slide--medical">
  <h2 class="slide-title" style="left:21px;top:30px">Inventory Highlights - <strong>Medical</strong></h2>
  <div class="segment" style="left:45px;top:69px">Point of Care <b>Clinics</b></div>
  <div class="segment" style="left:157px;top:69px">Medical Imaging <b>Centers</b></div>
  <div class="divider" style="left:148px;top:74px;height:193px"></div>

  <div class="stat" style="--x:62;--y:117"><span class="stat__icon"><svg><use href="#i-expand"/></svg></span><p class="stat__label">Massive<br>scale</p></div>
  <div class="stat" style="--x:114;--y:118"><span class="stat__icon"><svg><use href="#i-globe"/></svg></span><p class="stat__label">Nationwide</p></div>
  <div class="stat" style="--x:62;--y:181"><span class="stat__icon"><svg><use href="#i-play"/></svg></span><p class="stat__label">5000<br>screens</p></div>
  <div class="stat" style="--x:114;--y:173"><span class="stat__icon"><svg><use href="#i-dwell"/></svg></span><p class="stat__label">College grads<br>high dwell time</p></div>
  <div class="stat" style="--x:62;--y:244"><span class="stat__icon"><svg><use href="#i-viewer"/></svg></span><p class="stat__label">3M impressions<br>/month</p></div>
  <div class="stat" style="--x:186;--y:118"><span class="stat__icon"><svg><use href="#i-play"/></svg></span><p class="stat__label">50 screens</p></div>
  <div class="stat" style="--x:186;--y:175"><span class="stat__icon"><svg><use href="#i-viewer"/></svg></span><p class="stat__label">400k impressions/<br>month</p></div>
  <div class="stat" style="--x:186;--y:239"><span class="stat__icon"><svg><use href="#i-globe"/></svg></span><p class="stat__label">Northeast U.S.</p></div>

  <div class="badge-exclusive" style="left:219px;top:127px"><span>Exclusive<br>to<br>CoinCache</span></div>
  <div class="photo photo--medical" role="img" aria-label="Doctors reviewing notes beside a screen, and a clinic waiting room with wall displays"></div>
  <div class="badge-feature" style="left:277px;top:196px"><svg><use href="#i-pill"/></svg><span>Busy during<br>lockdown</span></div>
  <div class="footer footer--light" style="left:408px"><span class="footer__tag">DOOH NOW</span><span class="brand"><span class="brand__mark"></span>CoinCache</span></div>
</section>

<!-- Retail -->
<section class="slide slide--retail">
  <div class="photo photo--retail" role="img" aria-label="Shopper browsing vinyl records, and a grocery cashier beside a promotional screen"></div>
  <div class="badge-feature" style="left:175px;top:211px"><svg><use href="#i-spot"/></svg><span>Close to point<br>of purchase</span></div>
  <h2 class="slide-title" style="left:254px;top:29px">Inventory Highlights - <strong>Retail</strong></h2>
  <div class="segment" style="left:283px;top:70px">Urban Record <b>Stores</b></div>
  <div class="segment" style="left:395px;top:70px"><b>Grocery</b></div>
  <div class="divider" style="left:385px;top:75px;height:192px"></div>

  <div class="stat" style="--x:302;--y:119"><span class="stat__icon"><svg><use href="#i-play"/></svg></span><p class="stat__label">X screens</p></div>
  <div class="stat" style="--x:351;--y:119"><span class="stat__icon"><svg><use href="#i-income"/></svg></span><p class="stat__label">High income<br>Multiple<br>visits/month</p></div>
  <div class="stat" style="--x:302;--y:176"><span class="stat__icon"><svg><use href="#i-viewer"/></svg></span><p class="stat__label">X impressions<br>per month</p></div>
  <div class="stat" style="--x:302;--y:240"><span class="stat__icon"><svg><use href="#i-globe"/></svg></span><p class="stat__label">Nationwide</p></div>
  <div class="stat" style="--x:414;--y:119"><span class="stat__icon"><svg><use href="#i-play"/></svg></span><p class="stat__label">X screens</p></div>
  <div class="stat" style="--x:414;--y:176"><span class="stat__icon"><svg><use href="#i-viewer"/></svg></span><p class="stat__label">X impressions<br>per month</p></div>
  <div class="stat" style="--x:414;--y:241"><span class="stat__icon"><svg><use href="#i-globe"/></svg></span><p class="stat__label">Northeast U.S.</p></div>

  <div class="badge-exclusive" style="left:448px;top:130px"><span>Exclusive<br>to<br>CoinCache</span></div>
  <div class="footer" style="left:412px"><span class="footer__tag">DOOH NOW</span><span class="brand"><span class="brand__mark"></span>CoinCache</span></div>
</section>

<!-- Entertainment -->
<section class="slide slide--entertainment">
  <div class="photo photo--entertainment" role="img" aria-label="Sports bar with rows of wall screens, and a packed hockey arena with a centre scoreboard"></div>
  <div class="title-plate"></div>
  <h2 class="slide-title" style="left:21px;top:28px">Inventory Highlights - <strong>Entertainment</strong></h2>
  <div class="segment" style="left:48px;top:72px"><b>Bar/Restaurant</b></div>
  <div class="segment" style="left:149px;top:72px">Sports <b>Arenas</b></div>
  <div class="divider" style="left:141px;top:77px;height:193px"></div>

  <div class="stat" style="--x:65;--y:119"><span class="stat__icon"><svg><use href="#i-expand"/></svg></span><p class="stat__label">Massive<br>scale</p></div>
  <div class="stat" style="--x:114;--y:120"><span class="stat__icon"><svg><use href="#i-globe"/></svg></span><p class="stat__label">Nationwide</p></div>
  <div class="stat" style="--x:65;--y:181"><span class="stat__icon"><svg><use href="#i-play"/></svg></span><p class="stat__label">X screens</p></div>
  <div class="stat" style="--x:65;--y:233"><span class="stat__icon"><svg><use href="#i-viewer"/></svg></span><p class="stat__label">X impressions<br>per month</p></div>
  <div class="stat" style="--x:178;--y:120"><span class="stat__icon"><svg><use href="#i-play"/></svg></span><p class="stat__label">X screens</p></div>
  <div class="stat" style="--x:178;--y:175"><span class="stat__icon"><svg><use href="#i-viewer"/></svg></span><p class="stat__label">X impressions<br>per month</p></div>
  <div class="stat" style="--x:178;--y:237"><span class="stat__icon"><svg><use href="#i-globe"/></svg></span><p class="stat__label">Northeast U.S.</p></div>

  <div class="badge-exclusive" style="left:207px;top:110px"><span>Exclusive<br>to<br>CoinCache</span></div>
  <div class="badge-feature" style="left:254px;top:202px"><svg><use href="#i-field"/></svg><span>Sports<br>Fans</span></div>
</section>

<!-- High Net Worth -->
<section class="slide slide--networth">
  <div class="photo photo--networth" role="img" aria-label="Private airport lounge with chandelier, wood panelling and a wall screen"></div>
  <div class="badge-feature badge-feature--tilted" style="left:216px;top:207px"><span>Exclusive to<br>CoinCache</span></div>
  <h2 class="slide-title" style="left:295px;top:40px;line-height:24.5px">Inventory<br>Highlights –<br>High <strong>Net Worth</strong></h2>
  <div class="segment" style="left:444px;top:44px">Private <b>Airport</b></div>

  <div class="stat stat--large" style="--x:465;--y:98"><span class="stat__icon"><svg viewBox="0 0 36 36"><use href="#i-play"/></svg></span><p class="stat__label" style="margin-top:10px">X screens</p></div>
  <div class="stat stat--large" style="--x:465;--y:164"><span class="stat__icon"><svg viewBox="0 0 36 36"><use href="#i-viewer"/></svg></span><p class="stat__label" style="margin-top:10px">X impressions per<br>month</p></div>
  <div class="stat stat--large" style="--x:465;--y:235"><span class="stat__icon"><svg viewBox="0 0 36 36"><use href="#i-globe"/></svg></span><p class="stat__label" style="margin-top:10px">Nationwide</p></div>

  <div class="footer" style="left:412px"><span class="footer__tag">DOOH NOW</span><span class="brand"><span class="brand__mark"></span>CoinCache</span></div>
</section>

<div class="page-number">3</div>
</body>
</html>
```